Brell Stone Company Business Cards

Front and Back Business Card - logo and text setup - cool design. I need workable photoshop or illustrator files so I can setup each employee card with design that is created
Updates

Hi everyone, thank you for the great entries. Please no more white and blue cards - there are so many already - black and silver only now please. thanks!

Target Market(s)

Construction Industry - Facility Managers

Industry/Entity Type

Construction

Contact Information for Business Card

I really like contemporary simplistic looks - clean neat....not opposed to seeing some black backrounds

Requirements
Must have
• Logo/website address with design on front only - www.brellstone-example.com (logo attached)
• Back:
• Name/Title/Company Address/Phone/email address
Nice to have
• Cool design
Should not have
• Nothing gimmicky like Fire or Water - since we are a Fire Protection company - it has all been done

```html
<!DOCTYPE html>
<html lang="en">
<head>
<meta charset="utf-8">
<title>Brell Stone Company – Business Cards</title>
<link rel="stylesheet" href="https://fonts.googleapis.com/css2?family=Open+Sans:wght@400;700;800&display=swap">
<style>
  :root {
    --backdrop: #2a2a2c;
    --card: #000000;
    --brand-blue: #0a2a9c;
    --brand-red: #f42121;
    --ink-light: #ffffff;
    --font-main: "Open Sans", sans-serif;
  }
  * { box-sizing: border-box; margin: 0; padding: 0; }
  html, body {
    width: 1200px; height: 960px; overflow: hidden;
    background: var(--backdrop);
    font-family: var(--font-main);
  }
  .sheet { position: relative; width: 1200px; height: 960px; }
  .card {
    position: absolute; left: 210px;
    width: 780px; height: 446px;
    background: var(--card);
    overflow: hidden;
    box-shadow: 0 10px 30px rgba(0,0,0,.45);
  }
  .card--front { top: 30px; }
  .card--back { top: 488px; }

  .wordmark {
    font-weight: 800; color: var(--brand-blue);
    letter-spacing: -1px; line-height: 1; white-space: nowrap;
  }
  .card--front .wordmark {
    position: absolute; left: 0; right: 0; top: 150px;
    text-align: center; font-size: 76px;
  }
  .front-url {
    position: absolute; left: 0; right: 0; top: 268px;
    text-align: center; color: var(--ink-light);
    font-size: 19px; letter-spacing: 5px;
  }

  .card--back .wordmark {
    position: absolute; left: 58px; top: 46px; font-size: 58px;
  }
  .name-band {
    position: absolute; left: 0; top: 158px;
    width: 420px; height: 104px;
    background: var(--brand-red);
    padding: 20px 0 0 58px;
    color: var(--ink-light);
  }
  .person-name { font-weight: 700; font-size: 26px; line-height: 1.15; }
  .person-title { font-size: 24px; line-height: 1.2; }
  .address {
    position: absolute; left: 58px; top: 284px;
    color: var(--ink-light); font-size: 20px; line-height: 1.45;
  }
  .contact-band {
    position: absolute; left: 350px; top: 226px;
    width: 430px; height: 130px;
    background: var(--brand-blue);
  }
  .contact-list {
    position: absolute; left: 366px; top: 232px;
    list-style: none; color: var(--ink-light);
    font-size: 20px; line-height: 1;
  }
  .contact-list li { display: flex; align-items: center; height: 34px; }
  .contact-icon { width: 20px; height: 20px; margin-right: 22px; flex: none; }
</style>
</head>
<body>
<main class="sheet">
  <section class="card card--front" aria-label="Card front">
    <div class="wordmark">Brell Stone</div>
    <div class="front-url">www.brellstone-example.com</div>
  </section>

  <section class="card card--back" aria-label="Card back">
    <div class="wordmark">Brell Stone</div>
    <div class="name-band">
      <div class="person-name">Dana Marlow</div>
      <div class="person-title">President</div>
    </div>
    <address class="address" style="font-style:normal">
      48 Quarry Lane<br>Westbrook, NY 11900
    </address>
    <div class="contact-band"></div>
    <ul class="contact-list">
      <li>
        <svg class="contact-icon" viewBox="0 0 20 20" aria-hidden="true">
          <path d="M5 2l3 4-2 2c1 2 3 4 5 5l2-2 4 3-2 3C9 17 3 11 2 4z" fill="#fff"/>
        </svg>(555) 014-2290
      </li>
      <li>
        <svg class="contact-icon" viewBox="0 0 20 20" aria-hidden="true">
          <rect x="2" y="4" width="16" height="12" fill="#fff"/>
          <path d="M2 4l8 7 8-7" fill="none" stroke="#0a2a9c" stroke-width="1.5"/>
        </svg>info@brellstone-example.com
      </li>
      <li>
        <svg class="contact-icon" viewBox="0 0 20 20" aria-hidden="true">
          <g fill="none" stroke="#fff" stroke-width="1.6">
            <circle cx="10" cy="10" r="8"/>
            <ellipse cx="10" cy="10" rx="3.5" ry="8"/>
            <path d="M2 10h16M3.5 6h13M3.5 14h13"/>
          </g>
        </svg>www.brellstone-example.com
      </li>
    </ul>
  </section>
</main>
</body>
</html>
```